Redesign of an existing homepage

This site needs a redesign
https://www.wanderhof-kelbach.de
This page with the accommodation options is important for the customer
https://www.wanderhof-kelbach.de/gastgeber/
Till now there is a new logo. See attachment. That's all I have.
It would make sense to use the colors of the logo in the redesign.
footer.jpg.
I would put this info into the footer. The graphic (Infomaterial) is not needed.
a new menu - links.jpg
This info can be put in a new menu. Therefore the right column is gone and there is more space for the design.
NEW:
Please keep in mind that the Icons are important and shall be displayed under every accommodation

```html
<!DOCTYPE html>
<html lang="en">
<head>
<meta charset="utf-8">
<title>Ferienregion Kelbachtal – Holiday in the Rottal</title>
<link href="https://fonts.googleapis.com/css2?family=Playfair+Display:wght@400;500&family=Open+Sans:wght@400;600;700&display=swap" rel="stylesheet">
<style>
:root{
  --green:#7cb52e;
  --green-dark:#5f9420;
  --navy:#17243a;
  --navy-2:#2a3b55;
  --ink:#222a33;
  --muted:#5b6570;
  --pale:#eef5e2;
  --foot-text:#cfd6de;
  --white:#fff;
}
*{box-sizing:border-box;margin:0;padding:0}
html,body{width:1200px;height:4988px;overflow:hidden}
body{position:relative;font-family:"Open Sans",Arial,sans-serif;color:var(--ink);background:var(--white);font-size:13px;line-height:1.6}
.serif{font-family:"Playfair Display",Georgia,serif;font-weight:400}
.abs{position:absolute}
.btn{display:inline-block;background:var(--green);color:#fff;font-size:11px;font-weight:600;letter-spacing:.06em;text-transform:uppercase;padding:10px 22px;border-radius:2px}

.topbar{top:0;left:0;width:1200px;height:28px;background:var(--navy);color:#fff;font-size:11px;display:flex;justify-content:flex-end;align-items:center;padding-right:80px;gap:14px}
.topbar .dot{width:14px;height:14px;border-radius:50%;background:#fff;opacity:.85}

.hero{top:28px;left:0;width:1200px;height:892px;background:linear-gradient(180deg,#b9cfe4 0%,#d9e4ee 22%,#6f8b6a 42%,#466a3e 58%,#6fa7b8 70%,#3f6a52 86%,#2b4632 100%)}
.partners{top:44px;left:320px;display:flex;gap:40px}
.partners span{display:block;width:60px;height:60px;background:rgba(255,255,255,.9);border-radius:6px}
.partners-right{top:52px;left:790px;display:flex;gap:30px}
.partners-right span{display:block;width:140px;height:46px;background:rgba(255,255,255,.92);border-radius:3px}
.brand{top:150px;left:80px;width:200px;height:110px;background:#fff;display:flex;align-items:center;gap:12px;padding:0 16px;box-shadow:0 4px 12px rgba(0,0,0,.15)}
.brand i{width:30px;height:30px;border-radius:50%;background:var(--green);flex:none}
.brand b{font-size:14px;font-weight:700;color:var(--navy);line-height:1.25}
.nav{top:160px;left:300px;width:820px;height:48px;background:#fff;display:flex;align-items:center;padding:0 14px;gap:26px;font-size:12px;font-weight:600}
.nav a{color:var(--ink);text-decoration:none}
.nav a.on{color:var(--green);border-bottom:2px solid var(--green);padding-bottom:2px}
.nav .btn{margin-left:auto}
.hero-kicker{top:382px;left:80px;color:#fff;font-size:12px;letter-spacing:.14em;text-transform:uppercase;font-weight:600}
.hero-title{top:405px;left:80px;color:#fff;font-size:56px;line-height:1.1;width:300px}
.arrows{top:712px;left:1040px;display:flex;gap:8px}
.arrows span{width:36px;height:36px;background:rgba(0,0,0,.35);display:flex;align-items:center;justify-content:center}

.about-img{top:950px;left:220px;width:380px;height:360px;background:linear-gradient(135deg,#d58a46,#b8703a 40%,#6d8fb0 70%,#5d7b4d)}
.about-img2{top:1180px;left:330px;width:250px;height:170px;background:linear-gradient(160deg,#8fb2cf,#d9ebf2 50%,#6f9455);border:6px solid #fff}
.about{top:940px;left:648px;width:470px}
.about h2{font-size:44px;margin-bottom:14px}
.about p{font-size:12.5px;color:var(--muted);margin-bottom:12px}

.sec-title{left:0;width:1200px;text-align:center;font-size:44px}
.card{width:508px;height:330px;background:#fff;box-shadow:0 2px 12px rgba(0,0,0,.12);padding:18px}
.card .ph{position:absolute;top:18px;left:18px;width:190px;height:150px}
.card .info{position:absolute;top:18px;left:226px;right:18px}
.card h3{font-size:20px;line-height:1.2}
.card .addr{font-size:11px;color:var(--muted)}
.icons{display:flex;gap:6px;margin:8px 0}
.icons svg{width:18px;height:18px}
.card .from{font-size:11px;font-weight:700}
.card .price{font-size:26px;font-family:"Playfair Display",Georgia,serif}
.card .desc{position:absolute;top:184px;left:18px;right:18px;font-size:11px;color:var(--muted);line-height:1.65}

.rottal{top:2820px;left:0;width:1200px;height:740px;background:var(--pale)}
.rottal-img{top:2820px;left:600px;width:600px;height:740px;background:linear-gradient(90deg,var(--pale) 0%,#b7d0e5 22%,#c9d9c8 50%,#6f9a4e 75%,#4e7a33 100%)}
.rottal-text{top:2900px;left:200px;width:440px;text-align:center}
.rottal-text h2{font-size:44px;margin-bottom:18px}
.rottal-text p{font-size:12.5px;color:var(--muted);margin-bottom:14px}

.leisure-head{top:3620px;left:0;width:1200px;text-align:center}
.leisure-head h2{font-size:44px}
.leisure-head h4{font-size:22px;margin-top:4px}
.leisure-head .sub{font-weight:700;font-size:14px;margin-top:10px}
.leisure-head .lead{width:620px;margin:10px auto 0;color:var(--muted);font-size:12.5px}
.lcard{width:300px;height:460px;background:#fff;box-shadow:0 2px 12px rgba(0,0,0,.12);text-align:center}
.lcard .ph{height:210px}
.lcard h3{font-size:22px;margin-top:18px}
.lcard .tag{font-size:12px;color:var(--muted)}
.lcard p{font-size:12px;color:var(--muted);padding:10px 24px}
.lcard .more{font-size:11px;font-weight:700;text-decoration:underline}
.lcard.on{border:3px solid var(--green);top:3820px;height:480px}

.foot-band{top:4380px;left:0;width:1200px;height:120px;background:linear-gradient(180deg,#fff 0%,#8fa2b2 45%,var(--navy) 100%)}
.footer{top:4500px;left:0;width:1200px;height:488px;background:var(--navy)}
.fcol{top:4530px;color:var(--foot-text)}
.fcol h5{font-family:"Playfair Display",Georgia,serif;font-weight:400;font-size:20px;color:#fff;margin-bottom:10px;border-bottom:2px solid var(--green);display:inline-block;padding-bottom:2px}
.fcol ul{list-style:none;font-size:12px;line-height:2}
.fbrand{top:4540px;left:80px;display:flex;align-items:center;gap:12px}
.fbrand i{width:34px;height:34px;border-radius:50%;background:var(--green)}
.fbrand b{color:#fff;font-size:15px;line-height:1.25}
.social{top:4640px;left:80px;display:flex;gap:10px}
.social span{width:26px;height:26px;border-radius:50%;background:var(--green-dark)}
.contact li{display:flex;gap:8px;align-items:flex-start;margin-bottom:8px;line-height:1.5}
.contact svg{flex:none;margin-top:3px}
.bottom{top:4930px;left:80px;width:1040px;display:flex;justify-content:space-between;font-size:11px;color:var(--foot-text);border-top:1px solid var(--navy-2);padding-top:10px}
.totop{top:4880px;left:1130px;width:34px;height:34px;background:var(--green);display:flex;align-items:center;justify-content:center}
</style>
</head>
<body>

<div class="abs topbar"><span>Call us Now: <b>0612 / 470 215</b></span><span class="dot"></span><span class="dot"></span><span class="dot"></span></div>

<div class="abs hero" role="img" aria-label="Alpine lake with green meadows, forest and mountains under a summer sky"></div>
<div class="abs partners"><span></span><span></span><span></span></div>
<div class="abs partners-right"><span></span><span></span></div>
<div class="abs brand"><i></i><b>Ferienregion<br>Kelbachtal</b></div>
<nav class="abs nav">
  <a class="on">Home</a><a>About</a><a>Rottal</a><a>Unterkünfte</a><a>Veranstaltungen</a><a>Art and Culture</a>
  <span class="btn">Contact us</span>
</nav>
<div class="abs hero-kicker">Holiday in the Rottal</div>
<h1 class="abs hero-title serif">The most beautiful spot in Bavaria</h1>
<div class="abs arrows">
  <span><svg width="12" height="12" viewBox="0 0 12 12"><path d="M8 1 3 6l5 5" stroke="#fff" stroke-width="2" fill="none"/></svg></span>
  <span><svg width="12" height="12" viewBox="0 0 12 12"><path d="m4 1 5 5-5 5" stroke="#fff" stroke-width="2" fill="none"/></svg></span>
</div>

<div class="abs about-img" role="img" aria-label="Autumn village with church beneath mountains"></div>
<div class="abs about-img2" role="img" aria-label="Lake and green hills in summer"></div>
<section class="abs about">
  <h2 class="serif">About Us</h2>
  <p>Kelbach and the surrounding area have everything that makes life worth living.</p>
  <p>Culture and nature, joie de vivre and enjoyment, friendly and open-minded people...</p>
  <p>Whether churches, fountains or other architectural monuments – on a tour through the historic town you can discover many loving details for yourself.</p>
  <p>For those who enjoy exercise and fitness, there is "pure nature" in and around Kelbach. Here you can enjoy cycling, walking, hiking, golfing, horseback riding and swimming, or simply enjoy the peace and quiet.</p>
  <span class="btn">Learn more</span>
</section>

<h2 class="abs sec-title serif" style="top:1505px">Accommodation</h2>

<div class="abs card" style="top:1600px;left:80px"><div class="ph" role="img" aria-label="Apartment living room with wooden furniture" style="background:linear-gradient(135deg,#b98a5e,#e4d3bd)"></div><div class="info"><h3 class="serif">Holiday Apartment Lindner</h3><div class="addr">Wiesenweg 3, 84999 Kelbach</div><div class="icons"><svg viewBox="0 0 18 18"><rect x="2" y="2" width="14" height="14" rx="3" fill="var(--green)"/></svg><svg viewBox="0 0 18 18"><circle cx="9" cy="9" r="7" fill="var(--green)"/></svg><svg viewBox="0 0 18 18"><rect x="2" y="2" width="14" height="14" rx="3" fill="var(--navy)"/></svg><svg viewBox="0 0 18 18"><circle cx="9" cy="9" r="7" fill="var(--navy)"/></svg></div><div class="from">From:</div><div class="price">€ 42.00</div></div><p class="desc">The spacious attic apartment is on the first floor and features three separate bedrooms (2 double rooms, 1 single room), a large bathroom, a separate toilet, an eat-in kitchen, and a living room with a balcony. A cot, a highchair, and an extra bed are available, as are Wi-Fi, satellite TV, and a hi-fi system. The spacious quiet garden with its loungers and chairs is available for use. Two parking spaces are located in front of the house. Garage use is available for a fee.</p></div>

<div class="abs card" style="top:1600px;left:612px"><div class="ph" role="img" aria-label="White guesthouse with balconies and garden" style="background:linear-gradient(180deg,#a9c4de,#e8e8e2 50%,#6f9a4b)"></div><div class="info"><h3 class="serif">Holiday Apartment Lindner</h3><div class="addr">Wiesenweg 3, 84999 Kelbach</div><div class="icons"><svg viewBox="0 0 18 18"><rect x="2" y="2" width="14" height="14" rx="3" fill="var(--green)"/></svg><svg viewBox="0 0 18 18"><circle cx="9" cy="9" r="7" fill="var(--green)"/></svg><svg viewBox="0 0 18 18"><rect x="2" y="2" width="14" height="14" rx="3" fill="var(--navy)"/></svg><svg viewBox="0 0 18 18"><circle cx="9" cy="9" r="7" fill="var(--navy)"/></svg></div><div class="from">From:</div><div class="price">€ 42.00</div></div><p class="desc">The spacious attic apartment is on the first floor and features three separate bedrooms (2 double rooms, 1 single room), a large bathroom, a separate toilet, an eat-in kitchen, and a living room with a balcony. A cot, a highchair, and an extra bed are available, as are Wi-Fi, satellite TV, and a hi-fi system. The spacious quiet garden with its loungers and chairs is available for use. Two parking spaces are located in front of the house. Garage use is available for a fee.</p></div>

<div class="abs card" style="top:1960px;left:80px"><div class="ph" role="img" aria-label="Bright dining area in holiday apartment" style="background:linear-gradient(135deg,#c9a57d,#f1e7d6)"></div><div class="info"><h3 class="serif">Holiday Apartment Lindner</h3><div class="addr">Wiesenweg 3, 84999 Kelbach</div><div class="icons"><svg viewBox="0 0 18 18"><rect x="2" y="2" width="14" height="14" rx="3" fill="var(--green)"/></svg><svg viewBox="0 0 18 18"><circle cx="9" cy="9" r="7" fill="var(--green)"/></svg><svg viewBox="0 0 18 18"><rect x="2" y="2" width="14" height="14" rx="3" fill="var(--navy)"/></svg><svg viewBox="0 0 18 18"><circle cx="9" cy="9" r="7" fill="var(--navy)"/></svg></div><div class="from">From:</div><div class="price">€ 42.00</div></div><p class="desc">The spacious attic apartment is on the first floor and features three separate bedrooms (2 double rooms, 1 single room), a large bathroom, a separate toilet, an eat-in kitchen, and a living room with a balcony. A cot, a highchair, and an extra bed are available, as are Wi-Fi, satellite TV, and a hi-fi system. The spacious quiet garden with its loungers and chairs is available for use. Two parking spaces are located in front of the house. Garage use is available for a fee.</p></div>

<div class="abs card" style="top:1960px;left:612px"><div class="ph" role="img" aria-label="Farmhouse with flower boxes and red roof" style="background:linear-gradient(180deg,#9fbcd9,#d6c4a8 45%,#5e8a3c)"></div><div class="info"><h3 class="serif">Holiday Apartment Lindner</h3><div class="addr">Wiesenweg 3, 84999 Kelbach</div><div class="icons"><svg viewBox="0 0 18 18"><rect x="2" y="2" width="14" height="14" rx="3" fill="var(--green)"/></svg><svg viewBox="0 0 18 18"><circle cx="9" cy="9" r="7" fill="var(--green)"/></svg><svg viewBox="0 0 18 18"><rect x="2" y="2" width="14" height="14" rx="3" fill="var(--navy)"/></svg><svg viewBox="0 0 18 18"><circle cx="9" cy="9" r="7" fill="var(--navy)"/></svg></div><div class="from">From:</div><div class="price">€ 42.00</div></div><p class="desc">The spacious attic apartment is on the first floor and features three separate bedrooms (2 double rooms, 1 single room), a large bathroom, a separate toilet, an eat-in kitchen, and a living room with a balcony. A cot, a highchair, and an extra bed are available, as are Wi-Fi, satellite TV, and a hi-fi system. The spacious quiet garden with its loungers and chairs is available for use. Two parking spaces are located in front of the house. Garage use is available for a fee.</p></div>

<div class="abs card" style="top:2320px;left:80px"><div class="ph" role="img" aria-label="Guest bedroom with double bed" style="background:linear-gradient(135deg,#d9cdbd,#f4efe8 60%,#b79d80)"></div><div class="info"><h3 class="serif">Holiday Apartment Lindner</h3><div class="addr">Wiesenweg 3, 84999 Kelbach</div><div class="icons"><svg viewBox="0 0 18 18"><rect x="2" y="2" width="14" height="14" rx="3" fill="var(--green)"/></svg><svg viewBox="0 0 18 18"><circle cx="9" cy="9" r="7" fill="var(--green)"/></svg><svg viewBox="0 0 18 18"><rect x="2" y="2" width="14" height="14" rx="3" fill="var(--navy)"/></svg><svg viewBox="0 0 18 18"><circle cx="9" cy="9" r="7" fill="var(--navy)"/></svg></div><div class="from">From:</div><div class="price">€ 42.00</div></div><p class="desc">The spacious attic apartment is on the first floor and features three separate bedrooms (2 double rooms, 1 single room), a large bathroom, a separate toilet, an eat-in kitchen, and a living room with a balcony. A cot, a highchair, and an extra bed are available, as are Wi-Fi, satellite TV, and a hi-fi system. The spacious quiet garden with its loungers and chairs is available for use. Two parking spaces are located in front of the house. Garage use is available for a fee.</p></div>

<div class="abs card" style="top:2320px;left:612px"><div class="ph" role="img" aria-label="Holiday home with lawn and trees" style="background:linear-gradient(180deg,#a7c3df,#e6e2d8 45%,#6a9446)"></div><div class="info"><h3 class="serif">Holiday Apartment Lindner</h3><div class="addr">Wiesenweg 3, 84999 Kelbach</div><div class="icons"><svg viewBox="0 0 18 18"><rect x="2" y="2" width="14" height="14" rx="3" fill="var(--green)"/></svg><svg viewBox="0 0 18 18"><circle cx="9" cy="9" r="7" fill="var(--green)"/></svg><svg viewBox="0 0 18 18"><rect x="2" y="2" width="14" height="14" rx="3" fill="var(--navy)"/></svg><svg viewBox="0 0 18 18"><circle cx="9" cy="9" r="7" fill="var(--navy)"/></svg></div><div class="from">From:</div><div class="price">€ 42.00</div></div><p class="desc">The spacious attic apartment is on the first floor and features three separate bedrooms (2 double rooms, 1 single room), a large bathroom, a separate toilet, an eat-in kitchen, and a living room with a balcony. A cot, a highchair, and an extra bed are available, as are Wi-Fi, satellite TV, and a hi-fi system. The spacious quiet garden with its loungers and chairs is available for use. Two parking spaces are located in front of the house. Garage use is available for a fee.</p></div>

<div class="abs" style="top:2700px;left:0;width:1200px;text-align:center"><span class="btn">View all accommodation</span></div>

<div class="abs rottal"></div>
<div class="abs rottal-img" role="img" aria-label="Village church tower above red roofs and green fields"></div>
<section class="abs rottal-text">
  <h2 class="serif">Rottal</h2>
  <p>Kelbach and the surrounding area have everything that makes life worth living.</p>
  <p>Find peace and activity, culture and enjoyment... always combined with the warmth of your hosts and the positive attitude to life in this region. Here, you can forget everyday life and enjoy life consciously and at a slower pace.</p>
  <p>Explore the beautiful nature on a leisurely walk or bike ride through the rolling hills of the Rottal, past numerous sights.</p>
  <p>A wide variety of attractions for young and old, such as thermal baths, adventure pools, museums as well as numerous events and festivals guarantee eventful and unforgettable holidays.</p>
  <span class="btn">Learn more</span>
</section>

<section class="abs leisure-head">
  <h2 class="serif">Leisure time</h2>
  <h4 class="serif">Leisure in the Rottal</h4>
  <div class="sub">Leisure and relaxation for the whole family</div>
  <p class="lead">Enjoy peace and relaxation in nature – combined with select activities. Get active with cycling, walking, and hiking, or simply unwind. Explore the region according to your needs!</p>
</section>

<article class="abs lcard" style="top:3840px;left:130px"><div class="ph" role="img" aria-label="Angler at a quiet river" style="background:linear-gradient(180deg,#9bb8c9,#5c7d55)"></div><h3 class="serif">Fishing</h3><div class="tag">Fishing at Kelbach</div><p>Around the approximately 40 hectare fishing lakes in Kelbach, you'll find numerous fishing spots and a bait station.</p><span class="more">Read More</span></article>

<article class="abs lcard on" style="left:450px"><div class="ph" role="img" aria-label="Hot air balloon over hills at sunset" style="background:linear-gradient(180deg,#e6a25a,#c9663a 50%,#5b4b3f)"></div><h3 class="serif">Balloon rides</h3><div class="tag">Fly in a balloon</div><p>Balloon flights lift you gently over the Rottal with wide views across rivers, villages and the distant mountains.</p><span class="more">Read More</span></article>

<article class="abs lcard" style="top:3840px;left:770px"><div class="ph" role="img" aria-label="Market stall with fresh vegetables" style="background:linear-gradient(135deg,#b3452f,#d9a441 50%,#6b8c35)"></div><h3 class="serif">Direct Marketers</h3><div class="tag">Regional food from the farm</div><p>Fresh milk, eggs, honey, bread and vegetables sold directly at farms around Kelbach.</p><span class="more">Read More</span></article>

<div class="abs" style="top:4330px;left:0;width:1200px;text-align:center"><span class="btn">View all</span></div>

<div class="abs foot-band" role="img" aria-label="Faded mountain silhouette"></div>
<footer class="abs footer"></footer>
<div class="abs fbrand"><i></i><b>Ferienregion<br>Kelbachtal</b></div>
<div class="abs social"><span></span><span></span><span></span></div>

<div class="abs fcol" style="left:280px"><h5>Quick links</h5><ul><li>About Us</li><li>Services</li><li>Gallery</li><li>Blogs</li><li>Contact Us</li></ul></div>
<div class="abs fcol" style="left:430px"><h5>Links</h5><ul><li>Copyright</li><li>Legal</li><li>Privacy</li><li>Accessibility</li><li>Sitemap</li></ul></div>
<div class="abs fcol contact" style="left:570px;width:260px"><h5>Contact Us</h5><ul>
  <li><svg width="14" height="14" viewBox="0 0 14 14"><path d="M3 1h3l1 3-2 1a7 7 0 0 0 4 4l1-2 3 1v3c0 1-1 2-2 2A11 11 0 0 1 1 3c0-1 1-2 2-2z" fill="var(--green)"/></svg><span>Tel: 0612 / 470 215<br>Fax: 0612 / 470 216</span></li>
  <li><svg width="14" height="14" viewBox="0 0 14 14"><rect x="1" y="3" width="12" height="8" fill="none" stroke="var(--green)" stroke-width="1.5"/><path d="m1 3 6 5 6-5" fill="none" stroke="var(--green)" stroke-width="1.5"/></svg><span>info@wanderhof-kelbach.de</span></li>
  <li><svg width="14" height="14" viewBox="0 0 14 14"><path d="M7 1a4 4 0 0 1 4 4c0 3-4 8-4 8S3 8 3 5a4 4 0 0 1 4-4z" fill="var(--green)"/><circle cx="7" cy="5" r="1.5" fill="var(--navy)"/></svg><span>Tourist Association in Kelbach and surrounding area<br>Wiesenweg 3, 84999 Kelbach</span></li>
</ul></div>
<div class="abs fcol" style="left:880px;width:240px"><h5>Opening Hours:</h5><ul><li>Mon–Fri: 9:00 – 17:00</li><li>May–October</li><li>Sat: 9:00 – 12:00</li></ul>
  <h5 style="margin-top:14px">Information material</h5><div><span class="btn">Request information material</span></div></div>

<div class="abs bottom"><span>© 2022. All rights reserved.</span><span>Terms of use &nbsp;&nbsp;&nbsp; Privacy Policy</span></div>
<div class="abs totop"><svg width="12" height="12" viewBox="0 0 12 12"><path d="m1 8 5-5 5 5" stroke="#fff" stroke-width="2" fill="none"/></svg></div>

</body>
</html>
```